Film Poster

The poster is for a small short comedy film which we are sending to Festivals and hoping it gets picked up as a tv series and we do have a few interested parties who are waiting on the final cut of the film to then decide if they want to commission more episodes. The poster would be used throughout all advertising globally and we would promote you on a regular bases via social media of the film and website etc.
The Brief:
The poster needs to be in a professional format of a movie film poster. Please make sure you understand the presentation of a film poster.
Image attached which we would like to use on the poster (running image). Possibly using just the character cut out of the image and placed on a different background. Alternatively, you can redo an old poster which features the same character, this is also attached. I have also uploaded a few other stills that you can choose to work with.
There needs to be various text on the poster;
Title: Duke of the Footlights
Tagline: When the encore leaves you stranded.
Credit Block:
A Telmar Pictures production Written and Directed by Hal Eddington Producer Hal Eddington Co-Producer Judith Parrell Director of Photography Dimitri Kastelos
Updates
Hi everyone,
I just want to inform you all that we have now changed this project to "payment committed". A huge thank you to everyone for your fantastic submissions and for those of you who have taken our feedback on board. We are really pleased with the standard which is why we have now committed to payment. It will be a tough final decision for us, but we welcome you all to make our decision the hardest possible by submitting excellent designs. Whoever we choose to go with, there will certainly be a few more of you who we would love to keep in contact with afterwards regarding future work we may have for you so do feel free to direct us to other locations such as a website you may have where we can see more of your work and also any other contact details you would like us to have so we can keep you on our database.
Many thanks again to all of you for your continued efforts and best of luck to everyone! Any questions, please don't hesitate to contact me and I will get back to you as soon as I can.
Kind Regards,
Judith.
Can we please see the following credit block on the poster? Many Thanks, Judith.
A Telmar Pictures Production Hal Eddington "Duke of the Footlights" Rosalind Hart Jodie Pellworth-Arif Trevor Gould Beatrix Lundqvist Nadia Frost Katy Bell Lucy Tattersdale and Georgina Purcell Music by... ? Director of Photography Dimitri Kastelos Producer Hal Eddington Co-Producer Judith Parrell Written and Directed by Hal Eddington

```html
<!DOCTYPE html>
<html lang="en">
<head>
<meta charset="utf-8">
<title>Duke of the Footlights – Poster</title>
<link href="https://fonts.googleapis.com/css2?family=Oswald:wght@300;400;500&family=Noto+Serif:wght@400&display=swap" rel="stylesheet">
<style>
  :root {
    --backdrop: #000000;
    --sky-top: #ec8a55;
    --sky-mid: #d9a070;
    --haze: #a6a27a;
    --ground: #7aa99c;
    --ground-deep: #5f9a8a;
    --ink-white: #ffffff;
    --tagline-ink: #2b2c6e;
    --chevron: rgba(255, 236, 214, 0.55);
    --figure-core: #2d2fa8;
    --figure-edge: rgba(45, 47, 168, 0);
  }
  * { margin: 0; padding: 0; box-sizing: border-box; }
  html, body { width: 1200px; height: 1000px; overflow: hidden; background: var(--backdrop); }
  .canvas { position: relative; width: 1200px; height: 1000px; background: var(--backdrop); }

  .poster {
    position: absolute; left: 288px; top: 62px; width: 617px; height: 874px; overflow: hidden;
    background: linear-gradient(180deg, var(--sky-top) 0%, var(--sky-mid) 30%, var(--haze) 55%, var(--ground) 78%, var(--ground-deep) 100%);
  }
  .poster::after {
    content: ""; position: absolute; inset: 0;
    background: radial-gradient(ellipse at 90% 10%, rgba(255,200,160,0.35), transparent 55%);
  }

  .chevrons { position: absolute; left: 45px; top: 138px; width: 340px; height: 110px; z-index: 1; }

  .tagline {
    position: absolute; left: 83px; top: 178px; z-index: 2;
    font-family: "Noto Serif", Georgia, serif; font-size: 19px; color: var(--tagline-ink); letter-spacing: 0.2px;
  }

  .hero-figure {
    position: absolute; left: 0; top: 330px; width: 570px; height: 560px; z-index: 1;
    background: radial-gradient(ellipse 55% 50% at 52% 52%, var(--figure-core) 0%, rgba(45,47,168,0.75) 45%, var(--figure-edge) 100%);
  }

  .title {
    position: absolute; right: 47px; top: 215px; z-index: 3; text-align: right;
    font-family: "Oswald", "Arial Narrow", sans-serif; font-weight: 300; font-size: 84px; line-height: 82px;
    color: var(--ink-white); letter-spacing: 2px; text-transform: uppercase;
  }

  .credits {
    position: absolute; left: 0; right: 0; top: 758px; z-index: 3;
    display: flex; flex-direction: column; align-items: center;
    font-family: "Oswald", "Arial Narrow", sans-serif; font-weight: 400; color: var(--ink-white);
    text-transform: uppercase;
  }
  .credits .line {
    display: flex; align-items: center; justify-content: center; gap: 4px;
    height: 22.5px; font-size: 13px; line-height: 1; white-space: nowrap;
  }
  .credits .name { display: inline-block; }
  .credits .label {
    display: inline-flex; flex-direction: column; align-items: flex-end; justify-content: center;
    font-size: 5px; line-height: 5.5px; letter-spacing: 0.2px; text-align: right;
  }
  .credits .small { font-size: 8px; }
</style>
</head>
<body>
<main class="canvas">
  <section class="poster">
    <svg class="chevrons" viewBox="0 0 340 110" aria-hidden="true">
      <g fill="none" stroke="var(--chevron)" stroke-width="3">
        <polyline points="85,2 2,55 85,108 85,92 26,55 85,18 85,2"/>
        <polyline points="168,2 85,55 168,108 168,92 109,55 168,18 168,2"/>
        <polyline points="251,2 168,55 251,108 251,92 192,55 251,18 251,2"/>
        <polyline points="334,2 251,55 334,108 334,92 275,55 334,18 334,2"/>
      </g>
    </svg>

    <p class="tagline">when the encore leaves you stranded</p>

    <div class="hero-figure" role="img" aria-label="Cut-out photo of the lead character in a blue coat and sunglasses, scarf flying, leaning into a backward run"></div>

    <h1 class="title">Duke<br>of<br>the<br>Footlights</h1>

    <div class="credits">
      <p class="line"><span class="name">Studio Name Pictures</span><span class="small">presents a</span><span class="name">Producers</span><span class="small">a film by</span><span class="name">Script Writer Actor One Actor Two "Movie Title"</span></p>
      <p class="line"><span class="label"><span>Music</span><span>by</span></span><span class="name">The Musician</span><span class="label"><span>Costume</span><span>designer</span></span><span class="name">Designer Name</span><span class="label"><span>Edited</span><span>by</span></span><span class="name">Editors Name</span><span class="label"><span>Production</span><span>designer</span></span><span class="name">Designers Name</span><span class="label"><span>Director of</span><span>photography</span></span><span class="name">Cinematographer</span></p>
      <p class="line"><span class="label"><span>Executive</span><span>producer</span></span><span class="name">Ex Producer 1 Ex Producer 2</span><span class="label"><span>Produced</span><span>by</span></span><span class="name">Producer One Producer 2</span><span class="label"><span>Story</span><span>by</span></span><span class="name">Story Writer</span></p>
      <p class="line"><span class="label"><span>Screenplay</span><span>by</span></span><span class="name">Screen Writer</span><span class="label"><span>Directed</span><span>by</span></span><span class="name">Director Name</span></p>
    </div>
  </section>
</main>
</body>
</html>
```